Business Card Design

We are a company that provides stump grinding services for residential and commercial clients. Looking for a simple business card design that may have some type of graphic on the card that will tie in with the Tamsen name(Grizzly Bear, Paw Print, etc) . Possibly some foliage wrapping around part of the card? Would like to have a simple design that stands out because it is unique. We are working on getting the website set up and there is a simple graphic on the top of the page that came to mind when I mentioned the leaves.

Industry/Entity Type

Business

Contact Information for Business Card

Tamsen Stump Grinding 303-257-4788KodiakStumps.Com

Font styles to use
Serif

Requirements
Must have
• Business name
• Website Address
• Phone Number
Nice to have
• Graphics that would be associated with a Tamsen bear.
Should not have
• Nothing frilly

```html
<!DOCTYPE html>
<html lang="en">
<head>
<meta charset="utf-8">
<title>Tamsen Stump Grinding – Business Card</title>
<link rel="stylesheet" href="https://fonts.googleapis.com/css2?family=Marcellus+SC&family=Marcellus&display=swap">
<style>
  :root {
    --backdrop: #d9d9d9;
    --card-white: #ffffff;
    --card-dark: #1e1e1e;
    --card-dark-edge: #3a3a3a;
    --silver-light: #f2f2f2;
    --silver-dark: #8a8a8a;
    --ink: #111111;
    --contact-text: #f0f0f0;
  }
  html, body {
    margin: 0;
    width: 1200px;
    height: 900px;
    overflow: hidden;
    background: var(--backdrop);
  }
  .card {
    position: absolute;
    left: 75px;
    top: 150px;
    width: 1050px;
    height: 600px;
    box-shadow: 0 12px 30px rgba(0,0,0,0.25);
    overflow: hidden;
  }
  .card-art {
    position: absolute;
    inset: 0;
  }
  .brand {
    position: absolute;
    left: 90px;
    top: 240px;
    display: flex;
    align-items: center;
    gap: 22px;
  }
  .brand-dot {
    width: 110px;
    height: 110px;
    border-radius: 50%;
    background: var(--ink);
    flex: none;
  }
  .brand-name {
    font-family: "Marcellus", serif;
    color: var(--ink);
    font-weight: 400;
    line-height: 1.05;
    margin: 0;
  }
  .brand-name .primary {
    display: block;
    font-size: 58px;
    letter-spacing: 2px;
  }
  .brand-name .secondary {
    display: block;
    font-size: 26px;
    letter-spacing: 1px;
  }
  .contact {
    position: absolute;
    left: 590px;
    top: 190px;
    list-style: none;
    margin: 0;
    padding: 0;
    font-family: "Marcellus SC", serif;
    color: var(--contact-text);
    font-size: 30px;
    letter-spacing: 2px;
  }
  .contact li {
    display: flex;
    align-items: center;
    gap: 22px;
    margin-bottom: 14px;
  }
  .contact svg {
    width: 30px;
    height: 24px;
    flex: none;
  }
</style>
</head>
<body>
  <article class="card">
    <svg class="card-art" viewBox="0 0 1050 600" preserveAspectRatio="none" aria-hidden="true">
      <defs>
        <linearGradient id="dark-panel" x1="0" y1="0" x2="1" y2="1">
          <stop offset="0" stop-color="var(--card-dark-edge)"/>
          <stop offset="1" stop-color="var(--card-dark)"/>
        </linearGradient>
        <linearGradient id="silver-band" x1="0" y1="0" x2="1" y2="0">
          <stop offset="0" stop-color="var(--silver-dark)"/>
          <stop offset="0.5" stop-color="var(--silver-light)"/>
          <stop offset="1" stop-color="var(--silver-dark)"/>
        </linearGradient>
      </defs>
      <rect class="dark-panel" width="1050" height="600" fill="url(#dark-panel)"/>
      <path class="silver-band" d="M400 0 H455 Q700 300 520 600 H470 Q640 300 400 0 Z" fill="url(#silver-band)"/>
      <path class="white-panel" d="M0 0 H400 Q640 300 470 600 H0 Z" fill="var(--card-white)"/>
    </svg>

    <div class="brand">
      <span class="brand-dot"></span>
      <h1 class="brand-name">
        <span class="primary">Tamsen</span>
        <span class="secondary">Stump Grinding</span>
      </h1>
    </div>

    <ul class="contact">
      <li class="contact-phone">
        <svg viewBox="0 0 30 24" aria-hidden="true">
          <path d="M2 9 Q15 0 28 9 L25 12 L21 10 V7 Q15 5 9 7 V10 L5 12 Z" fill="var(--contact-text)"/>
          <rect x="7" y="13" width="16" height="9" rx="2" fill="var(--contact-text)"/>
        </svg>
        <span>303-555-0146</span>
      </li>
      <li class="contact-web">
        <svg viewBox="0 0 30 24" aria-hidden="true">
          <rect x="2" y="3" width="26" height="18" fill="none" stroke="var(--contact-text)" stroke-width="2"/>
          <path d="M2 3 L15 14 L28 3" fill="none" stroke="var(--contact-text)" stroke-width="2"/>
        </svg>
        <span>TamsenStumps.Com</span>
      </li>
    </ul>
  </article>
</body>
</html>
```